Marden Voss Advisory Webpage

I need to transition into a Wordpress website to be able to insert tracking code. This was a HostLark website, but now I'm limited on functionality

Here are requirements: I need to replicate mardenvoss.example

My company is focused in search and placement, consulting and workforce development for the turfgrass and hospitality industry

I'm also looking to integrate the following for a recruiting agency job board.
Multiple Dashboard view
✔ Job map
✔ Demo Content upload
✔ Chat button
✔ CV/Resume builder
✔ Featured job on top
✔ Email Alert
✔ Job bookmark
✔ Job CV package
✔ Social media Login
✔ SEO set up
✔ Plugin installation
✔ Featured jobs
✔ Payment gateway integration and set up
✔ Responsive design
Updates

Went on vacation/holiday

Target Market(s)

Golf and turfgrass businesses; as well as candidates for those companies

Industry/Entity Type

Turfgrass and Golf Industry

Coding

Coded - Design and coding required

Font styles to use
Sans Serif

Colors

Designer to choose colors to be used in the design.

Requirements
Must have
• Functionality of HostLark Web Design builder, Chat box capability, pop up capability, scheduling/appointment booking integration, ability to upload videos similar to my current website, e-commerce capabilities
Nice to have
• Everything to integrate "recruiting agency" aspect to collect information from potential candidates

```html
<!DOCTYPE html>
<html lang="en">
<head>
<meta charset="utf-8">
<title>Workforce Development – Marden Voss Advisory</title>
<link href="https://fonts.googleapis.com/css2?family=Poppins:wght@400;500;600&family=Open+Sans:wght@800&display=swap" rel="stylesheet">
<style>
:root{
  --brand:#3d4f47;
  --ink:#15171a;
  --body:#3a3d40;
  --footer:#0f1219;
  --footer-line:#2a2e36;
  --white:#fff;
  --chip:#4a4f55;
}
*{box-sizing:border-box;margin:0;padding:0}
html,body{width:717px;height:1200px;overflow:hidden;background:var(--white);font-family:'Poppins',sans-serif;color:var(--ink)}
.page{position:relative;width:717px;height:1200px}

.site-header{position:absolute;left:0;top:0;width:717px;height:77px;background:var(--white)}
.brand-box{position:absolute;left:59px;top:0;width:131px;height:105px;background:var(--white);border-radius:0 0 12px 12px;z-index:2;display:flex;flex-direction:column;align-items:center;justify-content:center;gap:6px}
.brand-mark{display:block;width:22px;height:22px;border-radius:50%;background:var(--brand)}
.brand-name{display:block;font-weight:600;font-size:12px;color:var(--brand);text-align:center;line-height:1.15}
.top-contact{position:absolute;top:10px;display:flex;align-items:center;gap:5px}
.top-contact .ico{flex:none;width:26px;height:26px;border-radius:50%;border:1px solid #9aa09c;display:flex;align-items:center;justify-content:center}
.top-contact .lbl{font-size:7px;color:#555;line-height:1}
.top-contact .val{font-size:9px;font-weight:500;color:var(--ink);line-height:1.3;white-space:nowrap}
.quote-btn{position:absolute;left:565px;top:10px;width:91px;height:25px;background:var(--brand);border-radius:13px 13px 0 13px;color:var(--white);font-size:8.5px;font-weight:600;display:flex;align-items:center;justify-content:center;gap:3px}
.main-nav{position:absolute;top:50px;right:60px;display:flex;gap:17px;font-size:8.8px;font-weight:500}
.main-nav a{color:var(--ink);text-decoration:none}
.main-nav a.active{color:var(--brand);border-bottom:1px solid var(--brand);padding-bottom:2px;margin-right:5px}

.hero{position:absolute;left:0;top:77px;width:717px;height:173px;background:linear-gradient(180deg,#5e7a3e 0%,#6f9240 40%,#55783a 75%,#3f4f36 100%);display:flex;align-items:center;justify-content:center}
.hero h1{font-family:'Open Sans',sans-serif;font-weight:800;font-size:25px;color:var(--white);letter-spacing:.3px;margin-top:3px}

.intro{position:absolute;left:72px;top:290px;width:573px;font-size:8.9px;line-height:17.2px;color:var(--body);text-align:justify;text-align-last:center}

.video-grid{position:absolute;left:59px;top:425px;width:598px;display:grid;grid-template-columns:repeat(3,193px);column-gap:10px;row-gap:0}
.video-card{text-align:center;height:253px}
.thumb{position:relative;height:129px;border-radius:4px}
.play{position:absolute;right:3px;top:5px;width:35px;height:22px;background:#2b2e31;border-radius:3px;display:flex;align-items:center;justify-content:center}
.video-card h3{font-size:11.6px;font-weight:500;line-height:16px;margin-top:7px;color:var(--ink)}
.video-card p{font-size:8.2px;line-height:15.6px;color:var(--body);margin-top:6px;padding:0 8px}

.site-footer{position:absolute;left:0;top:980px;width:717px;height:220px;background:var(--footer);color:var(--white)}
.foot-brand{position:absolute;left:78px;top:58px;width:108px;text-align:center}
.foot-brand .brand-mark{background:var(--white);margin:0 auto 8px}
.foot-brand .brand-name{color:var(--white)}
.socials{position:absolute;left:74px;top:150px;display:flex;gap:5px}
.socials span{width:23px;height:23px;border-radius:50%;background:#232730}
.foot-col{position:absolute;top:48px}
.foot-col h4{font-size:10.5px;font-weight:600;letter-spacing:.2px;margin-bottom:8px}
.quick-links{list-style:none;font-size:8.5px;line-height:18px}
.contact-row{display:flex;align-items:center;gap:7px;font-size:8.5px;line-height:13px;margin-bottom:9px}
.contact-row .ico{flex:none;width:24px;height:24px;border-radius:50%;background:var(--chip);display:flex;align-items:center;justify-content:center}
.newsletter p{font-size:8.3px;line-height:14px;width:140px}
.email-field{margin-top:10px;margin-left:-4px;width:146px;height:26px;border-radius:13px;background:var(--white);display:flex;align-items:center;justify-content:space-between;padding-left:11px;font-size:8.2px;color:#444}
.email-field .send{width:30px;height:26px;border-radius:13px;background:var(--brand);display:flex;align-items:center;justify-content:center}
.foot-rule{position:absolute;left:59px;top:185px;width:598px;height:1px;background:var(--footer-line)}
.copyright{position:absolute;left:0;top:198px;width:717px;text-align:center;font-size:8.5px}
</style>
</head>
<body>
<div class="page">

<header class="site-header">
  <div class="brand-box">
    <span class="brand-mark"></span>
    <span class="brand-name">MARDEN VOSS<br>ADVISORY</span>
  </div>
  <div class="top-contact" style="left:296px">
    <span class="ico"><svg width="11" height="11" viewBox="0 0 24 24"><path d="M6.6 10.8a15.1 15.1 0 006.6 6.6l2.2-2.2a1 1 0 011-.25 11.4 11.4 0 003.6.57 1 1 0 011 1V20a1 1 0 01-1 1A17 17 0 013 4a1 1 0 011-1h3.5a1 1 0 011 1 11.4 11.4 0 00.57 3.6 1 1 0 01-.25 1z" fill="none" stroke="#3a3d40" stroke-width="1.6"/></svg></span>
    <div><div class="lbl">CALL US</div><div class="val">555.014.2290</div></div>
  </div>
  <div class="top-contact" style="left:396px">
    <span class="ico"><svg width="12" height="10" viewBox="0 0 24 18"><rect x="1" y="1" width="22" height="16" rx="1.5" fill="#3a3d40"/><path d="M2 2l10 8 10-8" fill="none" stroke="#fff" stroke-width="1.6"/></svg></span>
    <div><div class="lbl">EMAIL</div><div class="val">mvoss.golf@example.com</div></div>
  </div>
  <div class="quote-btn">Get a Quote <svg width="8" height="8" viewBox="0 0 16 16"><circle cx="8" cy="8" r="8" fill="#fff"/><path d="M5 8h6M8.5 5l3 3-3 3" stroke="#3d4f47" stroke-width="1.8" fill="none"/></svg></div>
  <nav class="main-nav">
    <a href="#">HOME</a><a href="#">MARDEN VOSS</a><a href="#" class="active">WORKFORCE DEVELOPMENT</a><a href="#">NEWS</a><a href="#">CLIENTS</a><a href="#">CONTACT</a>
  </nav>
</header>

<section class="hero" role="img" aria-label="Golf course fairway with trees and a white clubhouse in the distance">
  <h1>WORKFORCE DEVELOPMENT</h1>
</section>

<p class="intro">Our workforce development system unifies businesses, job seekers, government and education to build sustainable talent solutions. Whether that is creating workforce training programs, collecting and sharing labor data, expanding career awareness through strategic outreach, Marden Voss Advisory enhances employer competitiveness and innovation while preparing job seekers for skill development, leadership training and career opportunities.  Learn more about about our workforce development initiatives and activities in a series of articles, videos and other free information.</p>

<section class="video-grid">
  <article class="video-card">
    <div class="thumb" role="img" aria-label="Video still of a panelist speaking from an office" style="background:linear-gradient(135deg,#7a6d5e,#3e3a36)"><span class="play"><svg width="9" height="10" viewBox="0 0 9 10"><path d="M0 0l9 5-9 5z" fill="#fff"/></svg></span></div>
    <h3>Golf Industry<br>Panel</h3>
    <p>Industry leaders discuss the state of the workforce, and how facilities can improve their recruitment and retention efforts.</p>
  </article>
  <article class="video-card">
    <div class="thumb" role="img" aria-label="Video still of a labor department speaker with a headset" style="background:linear-gradient(135deg,#c9b98a,#3d5a82)"><span class="play"><svg width="9" height="10" viewBox="0 0 9 10"><path d="M0 0l9 5-9 5z" fill="#fff"/></svg></span></div>
    <h3>Registered Apprenticeship:<br>Building Your Future Workforce</h3>
    <p>Dana Whitcomb, Regional Department of Labor, discusses the functionality &amp; benefits of Registered Apprenticeship to recruit &amp; develop skilled employees.</p>
  </article>
  <article class="video-card">
    <div class="thumb" role="img" aria-label="Video still of a turf specialist speaking" style="background:linear-gradient(135deg,#c9a86a,#8c6f4a)"><span class="play"><svg width="9" height="10" viewBox="0 0 9 10"><path d="M0 0l9 5-9 5z" fill="#fff"/></svg></span></div>
    <h3>Practical Turf Solutions During<br>a Labor Crisis</h3>
    <p>Grant Holloway, Owner of Greenline Turf Solutions, discusses industry best management practices for golf courses to employ during a labor shortage.</p>
  </article>
  <article class="video-card">
    <div class="thumb" role="img" aria-label="Video still of a school career supervisor speaking" style="background:linear-gradient(135deg,#b8a996,#4a4440)"><span class="play"><svg width="9" height="10" viewBox="0 0 9 10"><path d="M0 0l9 5-9 5z" fill="#fff"/></svg></span></div>
    <h3>How to Leverage School<br>Systems</h3>
    <p>Renee Caldwell, School to Career Transition Supervisor, Harbor County Public Schools discusses best practices on how businesses can leverage school systems to build your talent pipeline.</p>
  </article>
  <article class="video-card">
    <div class="thumb" role="img" aria-label="Video still of an immigration attorney speaking" style="background:linear-gradient(135deg,#d8d6d0,#8a7fc0)"><span class="play"><svg width="9" height="10" viewBox="0 0 9 10"><path d="M0 0l9 5-9 5z" fill="#fff"/></svg></span></div>
    <h3>Immigration and Connecting<br>the Seasonal Workforce</h3>
    <p>Marcus Ardent, Ardent Law and Season Link, discusses immigration pro's and con's, and a new solution to seasonal workforce needs.</p>
  </article>
  <article class="video-card">
    <div class="thumb" role="img" aria-label="Video still of a university professor in his office" style="background:linear-gradient(135deg,#a59a88,#4b4742)"><span class="play"><svg width="9" height="10" viewBox="0 0 9 10"><path d="M0 0l9 5-9 5z" fill="#fff"/></svg></span></div>
    <h3>Recruiting Interns and<br>College Graduates</h3>
    <p>Dr. Paul Kessler, Ridgeview State University, discusses student internships and how employers can engage with colleges.</p>
  </article>
</section>

<footer class="site-footer">
  <div class="foot-brand">
    <span class="brand-mark"></span>
    <span class="brand-name">MARDEN VOSS<br>ADVISORY</span>
  </div>
  <div class="socials"><span></span><span></span><span></span><span></span></div>

  <div class="foot-col" style="left:212px">
    <h4>QUICK LINKS</h4>
    <ul class="quick-links"><li>Home</li><li>Marden Voss</li><li>Workforce Development</li><li>Latest News</li><li>Recent Clients</li><li>Contact</li></ul>
  </div>

  <div class="foot-col" style="left:346px">
    <h4>CONTACT US</h4>
    <div class="contact-row"><span class="ico"><svg width="10" height="12" viewBox="0 0 20 24"><path d="M10 0a8 8 0 00-8 8c0 6 8 16 8 16s8-10 8-16a8 8 0 00-8-8zm0 11a3 3 0 110-6 3 3 0 010 6z" fill="#fff"/></svg></span><span>48 Alder Court, Fernbrook,<br>Ohio 43001, US</span></div>
    <div class="contact-row"><span class="ico"><svg width="10" height="10" viewBox="0 0 24 24"><path d="M6.6 10.8a15.1 15.1 0 006.6 6.6l2.2-2.2a1 1 0 011-.25 11.4 11.4 0 003.6.57 1 1 0 011 1V20a1 1 0 01-1 1A17 17 0 013 4a1 1 0 011-1h3.5a1 1 0 011 1 11.4 11.4 0 00.57 3.6 1 1 0 01-.25 1z" fill="#fff"/></svg></span><span>555.014.2290</span></div>
    <div class="contact-row"><span class="ico"><svg width="11" height="9" viewBox="0 0 24 18"><rect x="1" y="1" width="22" height="16" rx="1.5" fill="#fff"/><path d="M2 2l10 8 10-8" fill="none" stroke="#4a4f55" stroke-width="1.6"/></svg></span><span>mvoss.golf@example.com</span></div>
  </div>

  <div class="foot-col newsletter" style="left:514px">
    <h4>KEEP UPDATED</h4>
    <p>Sign up for our monthly newsletter and to receive alerts on latest career opportunities.</p>
    <div class="email-field"><span>Your Email</span><span class="send"><svg width="11" height="11" viewBox="0 0 24 24"><path d="M22 2L2 10l8 3 3 8z" fill="#fff"/></svg></span></div>
  </div>

  <div class="foot-rule"></div>
  <p class="copyright">Copyright © 2022 MVoss, LLC All rights reserved.</p>
</footer>

</div>
</body>
</html>
```